Coral Bay Pools New website

I currently operate a swimming pool service and repair business and looking for a re design for my website as it has been over 5 years since it was designed. current site is coralbaypoolslv.com

```html
<!DOCTYPE html>
<html lang="en">
<head>
<meta charset="utf-8">
<title>Coral Bay Pools</title>
<link rel="stylesheet" href="https://fonts.googleapis.com/css2?family=Montserrat:wght@600;700;800&family=Lato:wght@400;700&display=swap">
<style>
:root{
  --bg:#0f0f0f;
  --card:#1a1a1a;
  --orange:#f47a1f;
  --blue:#1456a8;
  --blue-deep:#0c3f86;
  --white:#ffffff;
  --muted:#d6d6d6;
  --line:#2a2a2a;
}
*{margin:0;padding:0;box-sizing:border-box}
html,body{width:1200px;height:4376px;overflow:hidden;background:var(--bg)}
body{position:relative;font-family:"Lato",sans-serif;color:var(--white)}
.abs{position:absolute}
.heading{font-family:"Montserrat",sans-serif;font-weight:700}
.btn{position:absolute;display:flex;align-items:center;justify-content:center;border-radius:22px;font-size:15px;color:var(--white)}
.btn-orange{background:var(--orange)}
.btn-outline{border:1.5px solid var(--white)}
.photo{position:absolute;border-radius:14px}

/* header */
.top-rule{position:absolute;left:0;top:0;width:1200px;height:3px;background:var(--orange)}
.site-header{position:absolute;left:0;top:3px;width:1200px;height:97px;background:#0b0b0b}
.nav-link{position:absolute;top:42px;font-size:15px;color:var(--white)}
.nav-link.active{color:var(--orange)}
.nav-link.active::after{content:"";position:absolute;left:0;right:0;bottom:-5px;height:2px;background:var(--orange)}
.brand{position:absolute;left:470px;top:14px;width:260px;height:180px;border-radius:30px;background:var(--white);display:flex;align-items:center;justify-content:center;z-index:3;font-family:"Montserrat",sans-serif;font-weight:800;font-size:26px;color:var(--blue)}

/* hero */
.hero{position:absolute;left:0;top:100px;width:1200px;height:600px;background:linear-gradient(100deg,#0a1426 0%,#1b2a45 35%,#4a3a2a 62%,#1c3b62 100%)}
.hero-title{position:absolute;left:109px;top:250px;font-family:"Montserrat",sans-serif;font-weight:800;font-size:44px;line-height:52px}
.hero-text{position:absolute;left:109px;top:372px;width:480px;font-size:22px;line-height:30px}
.dot{position:absolute;top:651px;width:9px;height:9px;border-radius:50%;border:1.5px solid var(--white)}
.dot.on{background:var(--white)}

.section-title{position:absolute;font-family:"Montserrat",sans-serif;font-weight:700;font-size:35px}
.center{left:0;width:1200px;text-align:center}
.lead{position:absolute;font-size:16px;line-height:26px;text-align:center}

.service-label{position:absolute;top:1258px;font-family:"Montserrat",sans-serif;font-weight:600;font-size:19px;display:flex;align-items:center;gap:16px}

.about-text{position:absolute;left:113px;top:1498px;width:420px;font-size:15.5px;line-height:26px;text-align:justify}

.why-box{position:absolute;left:226px;top:1958px;width:749px;height:324px;border-radius:20px;background:rgba(16,80,165,.88)}

.underline::after{content:"";position:absolute;left:0;bottom:-6px;width:45px;height:3px;background:var(--orange)}

.review{position:absolute;top:3467px;width:315px;height:216px;border-radius:4px;background:var(--card);padding:20px;font-size:13px;line-height:23px;color:var(--muted)}
.review.light{background:var(--white);color:#444}
.stars{color:var(--orange);font-size:15px;letter-spacing:2px;line-height:18px;margin-bottom:6px}
.reviewer{position:absolute;left:20px;top:155px;display:flex;align-items:center;gap:10px;font-size:13px;line-height:17px}
.avatar{width:38px;height:38px;border-radius:50%;background:linear-gradient(#8a9aa8,#4e5c68)}
.reviewer b{color:var(--blue);font-weight:700;display:block}
.quote{position:absolute;right:20px;top:150px;font-family:"Montserrat",sans-serif;font-size:56px;color:#555;line-height:56px}
.review.light .quote{color:#ccc}

.newsletter{position:absolute;left:0;top:3822px;width:1200px;height:133px;background:linear-gradient(90deg,var(--blue-deep),var(--blue),var(--blue-deep))}

.footer-head{position:absolute;top:4035px;font-family:"Montserrat",sans-serif;font-weight:600;font-size:18px}
.footer-link{position:absolute;font-size:15px}
.contact-row{position:absolute;left:113px;display:flex;align-items:center;gap:20px;font-size:15px}
.social{position:absolute;top:4226px;width:22px;height:22px;border-radius:50%;background:var(--white)}
</style>
</head>
<body>

<div class="top-rule"></div>
<header class="site-header">
  <span class="nav-link active" style="left:110px">Home</span>
  <span class="nav-link" style="left:203px">About Us</span>
  <span class="nav-link" style="left:316px">Our Services</span>
  <span class="nav-link" style="left:787px">Free Estimate</span>
  <span class="nav-link" style="left:931px">Blog</span>
  <span class="nav-link" style="left:1013px">Contact Us</span>
</header>
<div class="brand">Coral Bay Pools</div>

<section class="hero" role="img" aria-label="Modern house at dusk with lit interiors and an infinity pool"></section>
<h1 class="hero-title">YOUR DREAM POOL.<br>BUILT TO LAST.</h1>
<p class="hero-text">From new pool construction to renovations and repairs, we deliver high-quality craftsmanship you can trust.</p>
<span class="btn btn-orange" style="left:109px;top:494px;width:154px;height:42px">Free Estimate</span>
<span class="btn btn-outline" style="left:279px;top:494px;width:177px;height:42px">Start Your Project</span>
<span class="dot on" style="left:569px"></span>
<span class="dot" style="left:587px"></span>
<span class="dot" style="left:605px"></span>
<span class="dot" style="left:623px"></span>

<h2 class="section-title center" style="top:818px">Our Services</h2>
<p class="lead center" style="top:885px">When you invested in your pool, you knew it was a long-term investment in both money and time.<br>At home, it’s an oasis, a place to beat the heat and relax.</p>
<div class="photo" style="left:111px;top:970px;width:312px;height:267px;background:linear-gradient(135deg,#2b88c8,#6fc3e6 55%,#5b4a3c)" role="img" aria-label="Technician servicing a pool edge"></div>
<div class="photo" style="left:444px;top:970px;width:312px;height:267px;background:linear-gradient(180deg,#c9cfd6,#7a7f86 45%,#2a5fa8)" role="img" aria-label="Modern commercial building with a pool"></div>
<div class="photo" style="left:777px;top:970px;width:312px;height:267px;background:linear-gradient(180deg,#dde6ee,#8f8677 45%,#2a8fc4 70%,#6a9a4a)" role="img" aria-label="Residential home with a backyard pool"></div>
<span class="service-label" style="left:111px">Pool Services <svg width="26" height="16" viewBox="0 0 26 16"><path d="M1 8h22M16 1l7 7-7 7" fill="none" stroke="#f47a1f" stroke-width="2"/></svg></span>
<span class="service-label" style="left:444px">Commercial Pools <svg width="26" height="16" viewBox="0 0 26 16"><path d="M1 8h22M16 1l7 7-7 7" fill="none" stroke="#f47a1f" stroke-width="2"/></svg></span>
<span class="service-label" style="left:777px">Residential Pools <svg width="26" height="16" viewBox="0 0 26 16"><path d="M1 8h22M16 1l7 7-7 7" fill="none" stroke="#f47a1f" stroke-width="2"/></svg></span>

<h2 class="section-title underline" style="left:113px;top:1416px">About Us</h2>
<p class="about-text">When you need professional pool cleaning services in Nevada, you can count on the professionals at Coral Bay Pools to provide you with superior and prompt solutions. Whether you need assistance with a residential or commercial pool, we’ll vacuum, brush, and thoroughly clean your pool so it’s swim-ready.</p>
<span class="btn btn-orange" style="left:113px;top:1700px;width:179px;height:40px">Discover Our Story</span>
<div class="photo" style="left:680px;top:1416px;width:409px;height:306px;background:linear-gradient(180deg,#2f5fb8,#3a4d6e 45%,#5d4a36 80%,#2a3444)" role="img" aria-label="Glass-walled modern house at twilight"></div>
<div class="photo" style="left:620px;top:1550px;width:245px;height:205px;border:2px solid var(--bg);background:linear-gradient(180deg,#b7c9d8,#d9d2c4 45%,#3a8fc8)" role="img" aria-label="White villa with a poolside patio"></div>

<section class="abs" style="left:0;top:1900px;width:1200px;height:627px;background:linear-gradient(180deg,#aab8c6 0%,#55606b 45%,#2d6aa8 75%,#0f3a70 100%)" role="img" aria-label="Palm trees and poolside deck beside a modern home"></section>
<div class="why-box"></div>
<h2 class="section-title center" style="top:2017px;color:var(--white)">Why Choose Us?</h2>
<p class="lead center" style="top:2092px">Our full-service pool company proudly serves the entire Las Vegas valley, and we’re certified<br>by the Desert Valley Health Board to maintain the highest level of pool safety.</p>
<span class="btn btn-orange" style="left:523px;top:2170px;width:155px;height:42px">Contact Us</span>

<h2 class="section-title center" style="top:2646px">Our Projects</h2>
<p class="lead center" style="top:2714px">Explore a selection of custom pools designed and built with expert craftsmanship, premium<br>finishes, and attention to every detail.</p>
<div class="photo" style="left:111px;top:2805px;width:317px;height:172px;background:linear-gradient(180deg,#8fb6df,#3f6e3a 50%,#c9c7c2)" role="img" aria-label="Backyard pool with lounge chairs and trees"></div>
<div class="photo" style="left:443px;top:2805px;width:317px;height:172px;background:linear-gradient(135deg,#5fb6dc,#2a8bbf)" role="img" aria-label="Swimmer relaxing at the pool edge"></div>
<div class="photo" style="left:775px;top:2805px;width:318px;height:267px;border:2px solid var(--white);background:linear-gradient(180deg,#1d4b95,#123d80)" role="img" aria-label="Pool project with highlighted overlay"></div>
<span class="btn btn-orange" style="left:844px;top:2918px;width:180px;height:42px">Start Your Project</span>
<div class="photo" style="left:111px;top:2993px;width:317px;height:267px;background:linear-gradient(180deg,#9bb6cf,#e4e4e2 45%,#3b7fc0)" role="img" aria-label="White modern home with a front pool"></div>
<div class="photo" style="left:443px;top:2993px;width:317px;height:267px;background:linear-gradient(180deg,#6e8aa6,#5a3f2c 45%,#2a93a8 75%,#2e2a26)" role="img" aria-label="Covered patio with lounge chairs and pool at dusk"></div>
<div class="photo" style="left:775px;top:3087px;width:318px;height:173px;background:linear-gradient(135deg,#9fd6ea,#2b8fb8)" role="img" aria-label="Pool water with a cleaning tool"></div>

<h2 class="section-title underline" style="left:113px;top:3370px">What Our Clients Say</h2>
<p class="abs" style="left:670px;top:3375px;width:419px;font-size:15.5px;line-height:26px;text-align:justify">Real feedback from homeowners and businesses who trust us to build pools that last.</p>

<div class="review light" style="left:113px">
  <div class="stars">★★★★★</div>
  Lorem ipsum dolor sit amet, consectr adip iscing elit, sed do eiusmod tempo incididunt ut labore et dolore magna aliqua. Quis ipsum suspendisse ultric gravida.
  <div class="reviewer"><span class="avatar"></span><span><b>Mara Ellison</b>lorem ipsum</span></div>
  <span class="quote">“</span>
</div>
<div class="review" style="left:443px">
  <div class="stars">★★★★★</div>
  Lorem ipsum dolor sit amet, consectr adip iscing elit, sed do eiusmod tempo incididunt ut labore et dolore magna aliqua. Quis ipsum suspendisse ultric gravida.
  <div class="reviewer"><span class="avatar"></span><span><b>Mara Ellison</b>lorem ipsum</span></div>
  <span class="quote">“</span>
</div>
<div class="review" style="left:772px">
  <div class="stars">★★★★★</div>
  Lorem ipsum dolor sit amet, consectr adip iscing elit, sed do eiusmod tempo incididunt ut labore et dolore magna aliqua. Quis ipsum suspendisse ultric gravida.
  <div class="reviewer"><span class="avatar"></span><span><b>Mara Ellison</b>lorem ipsum</span></div>
  <span class="quote">“</span>
</div>

<section class="newsletter"></section>
<h2 class="section-title underline" style="left:113px;top:3862px">Stay Connected</h2>
<div class="abs" style="left:537px;top:3866px;width:426px;height:42px;border-radius:21px;background:var(--white);color:#222;font-size:14px;font-weight:700;padding:13px 28px">Email</div>
<span class="btn btn-orange" style="left:973px;top:3866px;width:116px;height:42px;font-weight:700">Submit</span>

<div class="abs heading" style="left:113px;top:4045px;font-size:34px">Coral Bay Pools</div>
<div class="contact-row" style="top:4127px"><svg width="18" height="18" viewBox="0 0 24 24"><path d="M5 3h4l2 5-3 2a12 12 0 0 0 6 6l2-3 5 2v4a2 2 0 0 1-2 2A18 18 0 0 1 3 5a2 2 0 0 1 2-2z" fill="none" stroke="#fff" stroke-width="1.6"/></svg>(702) 555-0148</div>
<div class="contact-row" style="top:4176px"><svg width="18" height="14" viewBox="0 0 24 18"><rect x="1" y="1" width="22" height="16" rx="2" fill="none" stroke="#fff" stroke-width="1.6"/><path d="M1 2l11 8 11-8" fill="none" stroke="#fff" stroke-width="1.6"/></svg>poolsolutions@coralbaypoolslv.com</div>
<span class="social" style="left:113px"></span>
<span class="social" style="left:169px"></span>
<span class="social" style="left:222px"></span>

<span class="footer-head" style="left:566px">Main Links</span>
<span class="footer-link" style="left:566px;top:4088px">Home</span>
<span class="footer-link" style="left:566px;top:4131px">Our Services</span>
<span class="footer-link" style="left:566px;top:4174px">Free Estimate</span>
<span class="footer-link" style="left:566px;top:4217px">Contact Us</span>
<span class="footer-head" style="left:781px">Company</span>
<span class="footer-link" style="left:781px;top:4088px">About Us</span>
<span class="footer-link" style="left:781px;top:4131px">Our Projects</span>
<span class="footer-link" style="left:781px;top:4174px">Testimonials</span>
<span class="footer-link" style="left:781px;top:4217px">Blog</span>
<span class="footer-head" style="left:991px">Resources</span>
<span class="footer-link" style="left:991px;top:4088px">Pool Care Tips</span>
<span class="footer-link" style="left:991px;top:4131px">Service Areas</span>
<span class="footer-link" style="left:991px;top:4174px">Testimonials</span>
<span class="footer-link" style="left:991px;top:4217px">Privacy Policy</span>

<div class="abs" style="left:1124px;top:4273px;width:54px;height:54px;border-radius:50%;background:var(--orange);display:flex;align-items:center;justify-content:center">
  <svg width="28" height="26" viewBox="0 0 28 26"><path d="M4 2h20a3 3 0 0 1 3 3v11a3 3 0 0 1-3 3H12l-6 5v-5H4a3 3 0 0 1-3-3V5a3 3 0 0 1 3-3z" fill="#fff"/><circle cx="9" cy="10.5" r="1.6" fill="#f47a1f"/><circle cx="14" cy="10.5" r="1.6" fill="#f47a1f"/><circle cx="19" cy="10.5" r="1.6" fill="#f47a1f"/></svg>
</div>

<div class="abs" style="left:0;top:4335px;width:1200px;height:1px;background:var(--line)"></div>
<p class="abs center" style="top:4349px;font-size:13px;text-align:center">Copyright © 2026 Coral Bay Pools. All rights reserved.</p>

</body>
</html>
```